Etikett für einen Rosé Wein
Zielgruppe
Wir sind ein Weingut und benötigen ein neues Etikett für unseren Muskattrollinger Rosé. Unsere Kunden sind eher traditionelle Weinkäufer.
Aufgabenstellung
Format:
Höhe: 9 cm
Breite: 11 cm
Da es nur ein Vorderetikett gibt, müssen alle relevanten Angaben (Hersteller, Alkohol, Inhalt in L, Rebsorte, etc.) enthalten sein. (siehe Flaschenabbildung anbei)
WÜRTTEMBERG
2019er
Muskattrollinger Rosé
DEUTSCHER QUALITÄTSWEIN
11,0 % Vol.
0,75 l
Enthält Sulfite
A.P.Nr. 58127364
Abfüller
Straße / PLZ / Ort / Tel.
Der Flaschenverschluss ist schwarz d.h. das neue Etikettendesign sollte dazu passen.
Bisher ist der Hintergrund des Weinetiketts schwarz. Dies muss jedoch nicht so bleiben.
Im Anhang finden Sie außerdem ein Plakat. Ggf. können Sie für das Flaschendesign einige nostalgische Elemente davon übernehmen.

```html
<!DOCTYPE html>
<html lang="de">
<head>
<meta charset="utf-8">
<title>Muskattrollinger Rosé – Etikett</title>
<link rel="stylesheet" href="https://fonts.googleapis.com/css2?family=EB+Garamond:wght@400;500;700&family=Allura&display=swap">
<style>
  :root {
    --page-bg: #2a1a14;
    --slate: #262626;
    --slate-light: #333231;
    --rust: #b34f2e;
    --rust-light: #c8684a;
    --accent: #c9481d;
    --ink-light: #f4f1ec;
  }
  html, body {
    margin: 0;
    padding: 0;
    width: 1100px;
    height: 1200px;
    overflow: hidden;
    background: var(--page-bg);
  }
  .label {
    position: absolute;
    left: 50px;
    top: 191px;
    width: 1000px;
    height: 818px;
    display: flex;
    font-family: "EB Garamond", Georgia, serif;
    color: var(--ink-light);
    box-shadow: 0 10px 30px rgba(0,0,0,.45);
  }
  .label__main {
    position: relative;
    width: 700px;
    height: 100%;
    overflow: hidden;
    background: linear-gradient(160deg, var(--slate-light), var(--slate) 55%, #1f1f1f);
  }
  .label__side {
    position: relative;
    width: 300px;
    height: 100%;
    background: linear-gradient(175deg, var(--rust-light), var(--rust) 40%, #a9472a);
  }
  .line {
    position: absolute;
    right: 38px;
    margin: 0;
    white-space: nowrap;
    text-align: right;
    line-height: 1;
  }
  .region {
    top: 38px;
    font-size: 74px;
    font-weight: 700;
    color: var(--accent);
    letter-spacing: 1px;
  }
  .vintage { top: 118px; font-size: 35px; font-weight: 500; }
  .variety {
    right: 36px;
    top: 205px;
    font-family: "Allura", cursive;
    font-size: 86px;
  }
  .style {
    right: 100px;
    top: 300px;
    font-family: "Allura", cursive;
    font-size: 104px;
  }
  .quality {
    top: 458px;
    font-size: 30px;
    color: var(--accent);
    line-height: 1.45;
    letter-spacing: 1px;
  }
  .small { font-size: 24px; font-weight: 500; }
  .apnr { top: 575px; }
  .bottler { top: 613px; }
  .marketer { top: 651px; color: var(--accent); }
  .address { top: 712px; }
  .address .gap { display: inline-block; width: 22px; }
  .phone { top: 750px; }
  .illustration {
    position: absolute;
    left: 30px;
    top: 20px;
    width: 270px;
    height: 450px;
    background: radial-gradient(ellipse at 55% 45%, rgba(245,225,215,.55), rgba(245,225,215,.18) 55%, rgba(245,225,215,0) 75%);
  }
  .facts {
    position: absolute;
    right: 48px;
    top: 632px;
    text-align: center;
  }
  .facts p { margin: 0; line-height: 1.15; }
  .volume { font-size: 36px; font-weight: 500; }
  .abv { font-size: 28px; font-weight: 500; margin-top: 8px !important; }
  .sulfite { font-size: 21px; font-weight: 500; }
</style>
</head>
<body>
  <div class="label">
    <section class="label__main">
      <h1 class="line region">Württemberg</h1>
      <p class="line vintage">2019 er</p>
      <p class="line variety">Muskattrollinger</p>
      <p class="line style">Rosé</p>
      <p class="line quality">DEUTSCHER<br>QUALITÄTSWEIN</p>
      <p class="line small apnr">A.P.Nr. 581 273 64</p>
      <p class="line small bottler">Abfüller D-BWW 581</p>
      <p class="line small marketer">vermarkted durch: Lukas Freitaler</p>
      <p class="line small address">Straße 5<span class="gap"></span>D-70412 Rebenhain - Talmühle</p>
      <p class="line small phone">Tel. 071 00/5550123</p>
    </section>
    <aside class="label__side">
      <div class="illustration" role="img" aria-label="Gravur-Illustration einer Weintraube mit Weinblatt in hellen Tönen"></div>
      <div class="facts">
        <p class="volume">0,75 l</p>
        <p class="abv">11,0% Vol.</p>
        <p class="sulfite">Enthalten Sulfit</p>
      </div>
    </aside>
  </div>
</body>
</html>
```